Business Card Design Project

Basic business card with minimal details. I just need company name, email & web address, telephone and my name.
I would like the back of the card to be grey with my logo & company name centred.

Target Market(s)

Architects
Builders
Property Developers

Industry/Entity Type

Business

Font styles to use
Sans Serif

Colors

Designer to choose colors to be used in the design.

Requirements
Must have
• Tallow Crest
Rupert Hazelby - Director
M: 0427 915203
E: rupert@tallowcrest.com.au
W: www.tallowcrest.com.au
Should not have
• No other images or pictures

```html
<!DOCTYPE html>
<html lang="en">
<head>
<meta charset="utf-8">
<title>Tallow Crest – Business Card</title>
<link rel="stylesheet" href="https://fonts.googleapis.com/css2?family=Titillium+Web:wght@400;600;700&display=swap">
<style>
  :root {
    --page-bg: #34302c;
    --card-bg: #ffffff;
    --brand-red: #c0283a;
    --slate: #5f7d92;
    --slate-dark: #56697a;
    --slate-text: #4f6a80;
    --band-start: #6c879c;
    --band-mid: #8ea8ba;
    --band-end: #5e788c;
    --band-text: #ffffff;
  }
  * { margin: 0; padding: 0; box-sizing: border-box; }
  html, body {
    width: 1200px;
    height: 900px;
    overflow: hidden;
    background: var(--page-bg);
    font-family: "Titillium Web", sans-serif;
  }
  .card {
    position: absolute;
    left: 60px;
    top: 140px;
    width: 1080px;
    height: 619px;
    background: var(--card-bg);
    border-radius: 24px;
    overflow: hidden;
  }
  .brand-square {
    position: absolute;
    left: 86px;
    top: 112px;
    width: 86px;
    height: 86px;
    background: var(--brand-red);
  }
  .brand-name {
    position: absolute;
    left: 258px;
    top: 108px;
    font-size: 72px;
    font-weight: 600;
    letter-spacing: 6px;
    line-height: 1;
    text-transform: uppercase;
    color: var(--slate);
    white-space: nowrap;
  }
  .person-name {
    position: absolute;
    left: 55px;
    top: 294px;
    font-size: 34px;
    font-weight: 700;
    line-height: 1.2;
    text-transform: uppercase;
    color: var(--brand-red);
    white-space: nowrap;
  }
  .name-divider {
    position: absolute;
    left: 362px;
    top: 296px;
    width: 2px;
    height: 46px;
    background: var(--slate-dark);
  }
  .person-title {
    position: absolute;
    left: 402px;
    top: 306px;
    font-size: 19px;
    line-height: 1.2;
    color: var(--brand-red);
  }
  .rule {
    position: absolute;
    left: 0;
    top: 343px;
    width: 100%;
    height: 3px;
    background: var(--slate-dark);
  }
  .address {
    position: absolute;
    left: 55px;
    top: 457px;
    font-size: 23px;
    line-height: 1.3;
    color: var(--slate-text);
    white-space: nowrap;
  }
  .contact-band {
    position: absolute;
    top: 500px;
    height: 62px;
    display: flex;
    align-items: center;
    color: var(--band-text);
    font-size: 24px;
    background: linear-gradient(90deg, var(--band-start), var(--band-mid) 55%, var(--band-end));
    white-space: nowrap;
  }
  .contact-web { left: 0; width: 380px; padding-left: 55px; }
  .contact-phone { left: 402px; width: 217px; justify-content: center; font-size: 26px; }
  .contact-email { left: 639px; width: 441px; justify-content: center; }
</style>
</head>
<body>
  <main class="card">
    <div class="brand-square" aria-hidden="true"></div>
    <div class="brand-name">Tallow Crest</div>

    <div class="person-name">Rupert Hazelby</div>
    <div class="name-divider" aria-hidden="true"></div>
    <div class="person-title">Director</div>
    <div class="rule" aria-hidden="true"></div>

    <div class="address">Address your Inc 00 4th Ave Marlow, NJ xxxxx</div>

    <div class="contact-band contact-web">www.tallowcrest.com.au</div>
    <div class="contact-band contact-phone">0427 915203</div>
    <div class="contact-band contact-email">rupert@tallowcrest.com.au</div>
  </main>
</body>
</html>
```